Veltrane Group Business Card Design

The CEO is looking for a new trendy look for his business card.
You can stay with current branding or come up with something new/creative. It can be 3D, including Medical Office buildings. You can use our logo in a variety of colors. Please include name, title, company name, company website, email address, cell number

Target Market(s)

Real Estate Development and Construction

Industry/Entity Type

Health care real estate

Contact Information for Business Card

Rohesh Kamdar, CEO M-604.781.2249 E-roheshkamdar@veltrane.com Address:4180 Lindqvist Ave, Tampa, FL 33482 www.veltrane.com

Font styles to use
Other font styles liked:
• Be creative

Requirements
Must have
• Creative, trendy look
Nice to have
• Please go to our website to get a feel- www. veltrane.com
Should not have
• small fonts

```html
<!DOCTYPE html>
<html lang="en">
<head>
<meta charset="utf-8">
<title>Veltrane Group – Business Card</title>
<link rel="stylesheet" href="https://fonts.googleapis.com/css2?family=Poppins:wght@400;700;800&display=swap">
<style>
  :root {
    --backdrop: #e9e6e1;
    --navy-light: #1b3263;
    --navy-dark: #040a1f;
    --card-white: #ffffff;
    --card-shade: #e4e4e4;
    --brand-red: #a51c2b;
    --ink-dark: #2a2a2a;
    --ink-grey: #555555;
    --rule: #c9c9c9;
    --white: #ffffff;
  }
  * { box-sizing: border-box; margin: 0; padding: 0; }
  html, body {
    width: 1200px;
    height: 900px;
    overflow: hidden;
    background: var(--backdrop);
    font-family: "Poppins", sans-serif;
  }
  .canvas {
    width: 1200px;
    height: 900px;
    display: flex;
    flex-direction: column;
    align-items: center;
    justify-content: center;
    gap: 50px;
  }
  .card {
    width: 640px;
    height: 366px;
    border-radius: 30px;
    box-shadow: 0 14px 30px rgba(0, 0, 0, 0.25);
    position: relative;
    display: flex;
    flex-direction: column;
    align-items: center;
  }
  .card--front {
    background: radial-gradient(ellipse at 50% 42%, var(--navy-light) 0%, var(--navy-dark) 75%);
    justify-content: center;
  }
  .card--back {
    background: linear-gradient(100deg, var(--card-shade) 0%, var(--card-white) 55%, var(--card-white) 100%);
    justify-content: center;
  }
  .wordmark {
    font-weight: 800;
    letter-spacing: -1px;
    line-height: 1;
  }
  .card--front .wordmark {
    color: var(--white);
    font-size: 68px;
    margin-top: 10px;
  }
  .front-web {
    color: var(--white);
    font-weight: 700;
    font-size: 15px;
    letter-spacing: 7px;
    margin-top: 70px;
  }
  .card--back .wordmark {
    color: var(--brand-red);
    font-size: 56px;
  }
  .holder-name {
    color: var(--brand-red);
    font-weight: 800;
    font-size: 21px;
    margin-top: 26px;
    line-height: 1.1;
  }
  .holder-title {
    color: var(--ink-dark);
    font-weight: 800;
    font-size: 16px;
    line-height: 1.2;
  }
  .divider {
    width: 470px;
    height: 1px;
    background: linear-gradient(90deg, transparent, var(--rule) 15%, var(--rule) 85%, transparent);
    margin: 16px 0 14px;
  }
  .contact-line {
    color: var(--ink-grey);
    font-size: 14.5px;
    line-height: 1.55;
    text-align: center;
  }
  .sep {
    color: var(--brand-red);
    font-weight: 700;
    margin: 0 5px;
  }
</style>
</head>
<body>
  <main class="canvas">
    <section class="card card--front">
      <div class="wordmark">Veltrane Group</div>
      <div class="front-web">www.veltrane.com</div>
    </section>

    <section class="card card--back">
      <div class="wordmark">Veltrane Group</div>
      <div class="holder-name">Rohesh Kamdar</div>
      <div class="holder-title">CEO</div>
      <div class="divider"></div>
      <p class="contact-line">T. 604.781.2249<span class="sep">|</span>roheshkamdar@veltrane.com</p>
      <p class="contact-line">4180 Lindqvist Ave, Tampa, FL 33482<span class="sep">|</span>www.veltrane.com</p>
    </section>
  </main>
</body>
</html>
```